Request for Business Card Design

Hi. My name is Marlene, I am looking for a new business card design for my company, Quarrow Signal Instruments, LLC. I really like the design you did for Tarsel Venture and was hoping you could do something similar using our full logo and our mark. I am also open to any raised texture design using our mark. I have attached our full logo, which would need to be somewhere on the card, as well as the mark in both outline and full form, as well as our brand colors / guide. The card does not have to be white, as long as our logo and mark appear. I actually like darker colored business cards more, but am open to all options. If you are interested in working with me, please let me know. We would also take the business card design into letterhead design if you can do that.

```html
<!DOCTYPE html>
<html lang="en">
<head>
<meta charset="utf-8">
<title>Quarrow Signal Instruments – Business Card</title>
<link href="https://fonts.googleapis.com/css2?family=Open+Sans:wght@400;600;700;800&display=swap" rel="stylesheet">
<style>
  :root {
    --backdrop: #1f1f1f;
    --card: #3c3c3e;
    --card-deep: #2e2e30;
    --brand-blue: #1a9bc7;
    --ink-light: #ffffff;
    --ink-soft: #d9d9d9;
    --rule: #8a8a8c;
  }
  * { box-sizing: border-box; margin: 0; padding: 0; }
  html, body {
    width: 1200px; height: 780px; overflow: hidden;
    background: var(--backdrop);
    font-family: "Open Sans", Arial, sans-serif;
  }
  .stage { position: relative; width: 1200px; height: 780px; }

  .card {
    position: absolute;
    width: 540px; height: 310px;
    background: var(--card);
    box-shadow: 0 14px 30px rgba(0,0,0,.55);
    overflow: hidden;
  }

  /* Back side */
  .card--back { left: 70px; top: 70px; }
  .texture-field {
    position: absolute; inset: 0;
    background: radial-gradient(ellipse at 95% 0%, #6a6a6c 0%, #3f3f41 40%, var(--card-deep) 100%);
  }
  .back-signature {
    position: absolute; right: 22px; bottom: 22px;
    display: flex; align-items: center; gap: 7px;
  }
  .brand-dot {
    width: 14px; height: 14px; border-radius: 50%;
    background: var(--brand-blue);
  }
  .brand-name {
    color: var(--ink-light);
    font-weight: 700;
    font-size: 11px;
    letter-spacing: .08em;
    text-transform: uppercase;
  }

  /* Front side */
  .card--front { left: 600px; top: 400px; }
  .front-brand {
    position: absolute; left: 150px; top: 58px;
    display: flex; align-items: center; gap: 14px;
  }
  .front-brand .brand-dot { width: 44px; height: 44px; }
  .front-brand .brand-name { font-size: 20px; line-height: 1.15; letter-spacing: .1em; }

  .person {
    position: absolute; right: 318px; top: 170px;
    text-align: right;
  }
  .person-name {
    color: var(--brand-blue);
    font-weight: 800; font-size: 30px; line-height: 1;
  }
  .person-role {
    color: var(--ink-light);
    font-weight: 600; font-size: 13px; margin-top: 4px;
  }
  .divider {
    position: absolute; left: 238px; top: 150px;
    width: 1px; height: 82px; background: var(--rule);
  }
  .contact-list {
    position: absolute; left: 254px; top: 152px;
    list-style: none;
  }
  .contact-list li {
    display: flex; align-items: center; gap: 8px;
    color: var(--ink-light); font-size: 12px; line-height: 20px;
  }
  .contact-list svg { width: 12px; height: 12px; fill: var(--brand-blue); flex: none; }

  .address-band {
    position: absolute; left: 0; right: 0; bottom: 30px; height: 28px;
    display: flex;
  }
  .address-band .band-blue {
    flex: 1; background: var(--brand-blue);
    color: var(--ink-light); font-size: 13px; font-weight: 600;
    display: flex; align-items: center; justify-content: center;
    letter-spacing: .02em;
  }
  .address-band .band-white { width: 56px; background: var(--ink-light); }
</style>
</head>
<body>
<main class="stage">

  <section class="card card--back" aria-label="Card back">
    <div class="texture-field" role="img" aria-label="Raised repeating brand mark texture fading from light grey at top right to dark grey"></div>
    <div class="back-signature">
      <span class="brand-dot"></span>
      <span class="brand-name">Quarrow Signal Instruments</span>
    </div>
  </section>

  <section class="card card--front" aria-label="Card front">
    <div class="front-brand">
      <span class="brand-dot"></span>
      <span class="brand-name">Quarrow<br>Signal Instruments</span>
    </div>

    <div class="person">
      <p class="person-name">Marlene</p>
      <p class="person-role">Director</p>
    </div>

    <div class="divider"></div>

    <ul class="contact-list">
      <li>
        <svg viewBox="0 0 24 24"><path d="M6.6 10.8a15 15 0 0 0 6.6 6.6l2.2-2.2a1 1 0 0 1 1-.25 11.4 11.4 0 0 0 3.6.6 1 1 0 0 1 1 1V20a1 1 0 0 1-1 1A17 17 0 0 1 3 4a1 1 0 0 1 1-1h3.5a1 1 0 0 1 1 1 11.4 11.4 0 0 0 .6 3.6 1 1 0 0 1-.25 1z"/></svg>
        +001 555 210 4832
      </li>
      <li>
        <svg viewBox="0 0 24 24"><path d="M6 2h10v6H6zM3 9h18v11H3zm3 3v2h4v-2zm0 4v2h4v-2zm8-4v6h4v-6z"/></svg>
        +001 555 210 4833
      </li>
      <li>
        <svg viewBox="0 0 24 24"><path d="M12 2a10 10 0 1 0 0 20 10 10 0 0 0 0-20zm0 2c1 1.3 1.8 3.4 2 6h-4c.2-2.6 1-4.7 2-6zm-7.9 8h4c.1 2.4.7 4.4 1.7 6A8 8 0 0 1 4.1 12zm0-2a8 8 0 0 1 5.7-6c-1 1.6-1.6 3.6-1.7 6zm7.9 10c-1-1.3-1.8-3.4-2-6h4c-.2 2.6-1 4.7-2 6zm2.2-2c1-1.6 1.6-3.6 1.7-6h4a8 8 0 0 1-5.7 6zm1.7-8c-.1-2.4-.7-4.4-1.7-6a8 8 0 0 1 5.7 6z"/></svg>
        www.quarrowsignal.com
      </li>
      <li>
        <svg viewBox="0 0 24 24"><path d="M3 5h18v14H3zm2 2v.5l7 5 7-5V7zm0 3v7h14v-7l-7 5z"/></svg>
        info@quarrowsignal.com
      </li>
    </ul>

    <div class="address-band">
      <p class="band-blue">1180 Meridian Park Road • Fairview, CO 80999</p>
      <span class="band-white"></span>
    </div>
  </section>

</main>
</body>
</html>
```